Wordpress Web Design & Coding for velcorahealth.ca

We need a website for a new investment company that is visually grabbing and vibrant. We would like to see a web page that displays trust, growth and confidence. Needs to be responsive and mobile friendly for all browsers and coded for both Android & IOS.

Open to the number of pages and menu items. I selected 4 but if you feel the layout would work better with less I am open to this. Need to sell the people (management team/related businesses) and then show where the invested money will be going (upcoming projects).

Company Info:

Vel Cora is an investment company put together by a group of seasoned business professionals who have come together to combine decades of success in the real estate development, management, financing and medical services. The company will be a full service company offering turn key solutions for medical professionals.

Vel-Cora will focus on providing a full range of services via a group of distinct companies to deliver newly emerging needs of the medical community. The end goal will be to create complete solutions for individuals in the medical community. Our group has experience and success with the conceptualization, construction and financing of medical and dental clinic spaces. Vel-Cora Solutions will be established to accommodate all areas of the development and creation of clinics for medical professionals from building construction to equipment financing and administrations.

You can mention these companies and take photos from their websites. You can also use stock photos.

Our construction partner:
https://318bld.com/projects/

Our equipment leasing partner:
https://www.norvixa.com/

Our Management Team and medical partners

Gil Parish
https://www.ourfirmstance.ca/

Dietmar Vellasquin
https://www.gshdentalservices.com/about-us

PROPOSED PROJECTS (see attachment for details)
Pinegrove Business Park
Holtmere Business Park
Mt. Corwin Ridge Professional

Target Market(s)

Investors

Industry/Entity Type

Investment

Coding

Coded - Design and coding required

Number of Pages Required

4 page

Font styles to use
Sans Serif

Requirements
Must have
• Wordpress – must be both desktop and mobile friendly with fast page load speed
Ability to edit after ourselves in Wordpress
Attractive home page with logo etc.
Logo colours are: for the blue the pantone color is #0355a3
and for the green is #8cc63f

Sections, about us, what we do/services we provide, contact us

```html
<!DOCTYPE html>
<html lang="en">
<head>
<meta charset="utf-8">
<title>Vel-Cora Solutions</title>
<link href="https://fonts.googleapis.com/css2?family=Montserrat:wght@400;500;600;700;800&display=swap" rel="stylesheet">
<style>
:root{
  --blue:#0355a3;
  --navy:#0b3a7e;
  --green:#8cc63f;
  --green-dark:#76b82a;
  --ink:#1a1a1a;
  --body:#6b6b6b;
  --grey-bg:#efefef;
  --line:#d6d6d6;
  --footer:#161a24;
}
*{box-sizing:border-box;margin:0;padding:0}
html,body{width:1200px;height:4434px;overflow:hidden}
body{font-family:'Montserrat',sans-serif;color:var(--ink);background:#fff;position:relative}
.abs{position:absolute}
.center{text-align:center;left:0;right:0}
.btn{position:absolute;display:flex;align-items:center;justify-content:center;color:#fff;font-weight:600;border-radius:40px;background:linear-gradient(90deg,var(--blue) 0%,var(--blue) 35%,var(--green) 100%)}
.heading{position:absolute;left:0;right:0;text-align:center;font-size:46px;font-weight:600;letter-spacing:.5px;text-transform:uppercase}
.heading b{color:var(--green);font-weight:800}

/* header */
.site-header{position:absolute;top:0;left:0;width:1200px;height:95px;background:#fff}
.brand{position:absolute;left:88px;top:18px;display:flex;align-items:center;gap:10px}
.brand-mark{width:22px;height:22px;background:var(--green)}
.brand-name{font-size:24px;font-weight:700;color:var(--blue);line-height:1;letter-spacing:.5px}
.brand-name small{display:block;font-size:13px;letter-spacing:2px;margin-top:4px}
.contact-chip{position:absolute;top:26px;display:flex;gap:14px;align-items:center}
.chip-icon{width:42px;height:42px;background:var(--blue);display:flex;align-items:center;justify-content:center}
.chip-label{font-size:13px;color:var(--green-dark);font-weight:500}
.chip-value{font-size:16px;font-weight:600;margin-top:6px}
.round-btn{position:absolute;top:26px;width:44px;height:44px;border-radius:50%;background:var(--blue);display:flex;align-items:center;justify-content:center}
.main-nav{position:absolute;top:95px;left:0;width:1200px;height:55px;background:var(--green);display:flex;align-items:center}
.main-nav a{position:absolute;color:#fff;text-decoration:none;font-size:15px;font-weight:500}
.main-nav a.active{color:var(--blue)}

/* hero */
.hero{position:absolute;top:150px;left:0;width:1200px;height:830px;overflow:hidden}
.hero-photo{position:absolute;inset:0;background:linear-gradient(100deg,#7f8790 0%,#c9ced4 35%,#eef0f2 55%,#dfe3e8 75%,#9aa5b2 100%)}
.hero-title{top:162px;font-size:58px;font-weight:700;color:#222}
.hero-sub{top:245px;font-size:23px;line-height:39px;color:#222}
.hero-wave{position:absolute;left:0;top:480px}

/* about */
.about-text{position:absolute;left:130px;width:940px;text-align:center;font-size:14px;line-height:27px;color:var(--body)}

/* services */
.services{position:absolute;top:1338px;left:0;width:1200px;height:708px;background:var(--grey-bg)}
.card{position:absolute;top:239px;width:324px;height:326px;background:#fff;border:1px solid var(--line);text-align:center}
.card svg{margin-top:40px}
.card h3{font-size:24px;font-weight:700;color:var(--navy);margin-top:24px;line-height:31px}
.card p{font-size:13.5px;line-height:25px;color:var(--body);margin:14px 26px 0}
.card a{display:block;margin-top:18px;font-size:15px;font-weight:600;color:var(--navy);text-decoration:none}
.slide-arrow{position:absolute;width:44px;height:44px;border-radius:50%;border:1.5px solid #8a8a8a;background:#fff;display:flex;align-items:center;justify-content:center}

/* company */
.company-photo{position:absolute;left:96px;top:2150px;width:424px;height:424px;border-radius:50%;background:radial-gradient(circle at 45% 40%,#c9a78a 0%,#6f5a4b 35%,#2e4a44 70%,#8b7668 100%)}
.company-ring{position:absolute;left:84px;top:2138px}
.company-title{position:absolute;left:579px;top:2172px;font-size:46px;font-weight:600}
.company-title b{color:var(--green);font-weight:800}
.company-text{position:absolute;left:579px;top:2248px;width:540px;font-size:14px;line-height:31.3px;color:var(--body);text-align:justify}

/* testimonials */
.testimonials{position:absolute;top:2686px;left:0;width:1200px;height:631px;background:linear-gradient(160deg,#0d3f8f 0%,#0a4aa0 45%,#0f57b3 75%,#0a3b85 100%)}
.testimonials .heading{color:#fff;font-weight:700;top:190px}
.quote-mark{top:240px;font-size:110px;line-height:110px;color:#fff;font-weight:800;height:80px;overflow:hidden}
.quote-text{top:318px;left:160px;right:160px;font-size:21.5px;line-height:36px;color:#fff}
.quote-name{top:432px;font-size:19px;font-weight:700;color:#fff}

/* contact */
.field{position:absolute;border:1px solid #c8c8c8;background:#fff;font-size:13.5px;color:#666;padding:16px 19px}

/* footer */
.footer-photo{position:absolute;left:0;top:3780px;width:1200px;height:654px;background:linear-gradient(180deg,#262c38 0%,#1a1f2a 45%,#11141b 100%)}
.footer-wave{position:absolute;left:0;top:3690px}
.foot-brand{position:absolute;left:0;right:0;top:4030px;text-align:center;font-size:34px;font-weight:700;color:var(--blue);line-height:1.05;letter-spacing:1px}
.foot-brand small{display:block;font-size:20px;letter-spacing:3px}
.foot-icon{position:absolute;top:4160px;width:84px;height:84px;border-radius:50%;background:var(--blue);display:flex;align-items:center;justify-content:center}
.foot-text{position:absolute;top:4256px;width:360px;text-align:center;font-size:17px;line-height:29px;color:#fff}
.copyright{top:4350px;font-size:15px;color:#fff}
.social{position:absolute;top:4388px;width:30px;height:30px;border-radius:50%;border:1.5px solid #fff}
</style>
</head>
<body>

<header class="site-header">
  <div class="brand"><span class="brand-mark"></span><div class="brand-name">VEL-CORA<small>SOLUTIONS</small></div></div>
  <div class="contact-chip" style="left:508px">
    <div class="chip-icon"><svg width="20" height="20" viewBox="0 0 24 24"><path d="M6.6 10.8a15 15 0 0 0 6.6 6.6l2.2-2.2c.3-.3.7-.4 1-.2 1.1.4 2.3.6 3.6.6.6 0 1 .4 1 1V20c0 .6-.4 1-1 1A17 17 0 0 1 3 4c0-.6.4-1 1-1h3.5c.6 0 1 .4 1 1 0 1.3.2 2.5.6 3.6.1.3 0 .7-.2 1z" fill="#fff"/></svg></div>
    <div><div class="chip-label">Call us</div><div class="chip-value">604-555-0147</div></div>
  </div>
  <div class="contact-chip" style="left:710px">
    <div class="chip-icon"><svg width="22" height="20" viewBox="0 0 24 22"><path d="M2 9l10-7 10 7v11H2z" fill="#fff"/><path d="M2 9l10 7 10-7" fill="none" stroke="#0355a3" stroke-width="1.6"/></svg></div>
    <div><div class="chip-label">Send us a mail</div><div class="chip-value">hello@velcorahealth.ca</div></div>
  </div>
  <div class="round-btn" style="left:967px"></div>
  <div class="round-btn" style="left:1017px"></div>
  <div class="round-btn" style="left:1067px"><svg width="16" height="16" viewBox="0 0 16 16"><circle cx="6.5" cy="6.5" r="4.5" fill="none" stroke="#fff" stroke-width="2"/><path d="M10 10l4 4" stroke="#fff" stroke-width="2.2" stroke-linecap="round"/></svg></div>
</header>

<nav class="main-nav">
  <a class="active" style="left:140px">Home</a>
  <a style="left:251px">About Us</a>
  <a style="left:386px">What We Do</a>
  <a style="left:548px">Partners</a>
  <a style="left:677px">Company Profile</a>
  <a style="left:873px">Blog</a>
  <a style="left:970px">Contact Us</a>
</nav>

<section class="hero">
  <div class="hero-photo" role="img" aria-label="Glass office building interior overlooking a city skyline"></div>
  <h1 class="abs center hero-title">VEL-CORA SOLUTIONS</h1>
  <p class="abs center hero-sub">Lorem ipsum dolor sit amet, consectetur adipiscing elit, sed do eiusmod tempor<br>incididunt ut labore et dolore magna aliqua.</p>
  <div class="btn" style="left:501px;top:346px;width:196px;height:55px;font-size:18px">Get Started</div>
  <svg class="hero-wave" width="1200" height="350" viewBox="0 0 1200 350">
    <path d="M0 320 C200 240 420 160 640 210 C850 250 1050 300 1200 480 L1200 350 L0 350Z" fill="#fff"/>
    <path d="M0 320 C200 200 450 120 700 150 C900 170 1080 230 1200 330 L1200 480 C1050 300 850 200 640 195 C420 190 200 260 0 330Z" fill="#8cc63f"/>
    <path d="M0 335 C220 255 430 190 640 205 C860 222 1060 300 1200 490 L1200 350 L0 350Z" fill="#fff"/>
  </svg>
</section>

<section class="about">
  <h2 class="heading" style="top:936px">About <b>US</b></h2>
  <p class="about-text" style="top:1004px">Lorem ipsum dolor sit amet, consectetur adipiscing elit, sed do eiusmod tempor incididunt ut labore et dolore magna aliqua. Ut enim ad minim veniam, quis nostrud exercitation ullamco laboris nisi ut aliquip ex ea commodo consequat. Duis aute irure dolor in reprehenderit in voluptate velit esse cillum dolore eu fugiat nulla pariatur</p>
  <p class="about-text" style="top:1111px">Lorem ipsum dolor sit amet, consectetur adipiscing elit, sed do eiusmod tempor incididunt ut labore et dolore magna aliqua. Ut enim ad minim veniam, quis nostrud exercitation ullamco laboris nisi ut aliquip ex ea commodo consequat.</p>
  <div class="btn" style="left:527px;top:1197px;width:145px;height:40px;font-size:15px">Read More</div>
</section>

<section class="services">
  <h2 class="heading" style="top:130px">What we <b>DO</b></h2>
  <div class="slide-arrow" style="left:9px;top:379px"><svg width="12" height="16" viewBox="0 0 12 16"><path d="M9 2L3 8l6 6" fill="none" stroke="#555" stroke-width="2"/></svg></div>
  <div class="slide-arrow" style="left:1146px;top:379px"><svg width="12" height="16" viewBox="0 0 12 16"><path d="M3 2l6 6-6 6" fill="none" stroke="#555" stroke-width="2"/></svg></div>
  <article class="card" style="left:90px">
    <svg width="54" height="54" viewBox="0 0 54 54"><rect x="4" y="10" width="34" height="40" fill="none" stroke="#8cc63f" stroke-width="2"/><path d="M12 40l26-28 6 6-26 28H12z" fill="none" stroke="#8cc63f" stroke-width="2"/><path d="M10 20h14M10 28h8" stroke="#8cc63f" stroke-width="2"/></svg>
    <h3>Construction</h3>
    <p>Lorem ipsum dolor sit amet, turiscing elit, sed do eiusmod tempor incididunt ut labore et dolore magna aliqua.</p>
    <a>Read More</a>
  </article>
  <article class="card" style="left:439px">
    <svg width="54" height="54" viewBox="0 0 54 54"><path d="M14 48V36c-6-5-8-12-5-19 3-8 12-12 21-10 9 2 14 10 13 18l4 8h-5v6h-8v9" fill="none" stroke="#8cc63f" stroke-width="2"/><circle cx="27" cy="22" r="7" fill="none" stroke="#0355a3" stroke-width="2"/><path d="M27 18v8M23 22h8" stroke="#0355a3" stroke-width="2"/></svg>
    <h3>Medical Solution</h3>
    <p>Lorem ipsum dolor sit amet, turiscing elit, sed do eiusmod tempor incididunt ut labore et dolore magna aliqua.</p>
    <a>Read More</a>
  </article>
  <article class="card" style="left:787px">
    <svg width="54" height="54" viewBox="0 0 54 54"><rect x="22" y="4" width="16" height="30" fill="none" stroke="#8cc63f" stroke-width="2"/><path d="M26 10h8M26 16h8M26 22h8M26 28h8" stroke="#8cc63f" stroke-width="2"/><path d="M4 40h12l10 4h14l8-6v6l-10 8H18L4 48" fill="none" stroke="#8cc63f" stroke-width="2"/></svg>
    <h3>Real Estate<br>Development</h3>
    <p>Lorem ipsum dolor sit amet, turiscing elit, sed do eiusmod tempor incididunt ut labore et dolore magna aliqua.</p>
    <a style="margin-top:12px">Read More</a>
  </article>
</section>

<section class="company">
  <svg class="company-ring" width="448" height="448" viewBox="0 0 448 448"><defs><linearGradient id="ringGrad" x1="0" y1="0" x2="1" y2="1"><stop offset="0" stop-color="#0355a3"/><stop offset=".55" stop-color="#8cc63f"/></linearGradient></defs><circle cx="224" cy="224" r="220" fill="none" stroke="url(#ringGrad)" stroke-width="6"/></svg>
  <div class="company-photo" role="img" aria-label="Smiling businessman in a green sweater signing papers in an office"></div>
  <h2 class="company-title">OUR <b>COMPANY</b></h2>
  <p class="company-text">Lorem ipsum dolor sit amet, consectetur adipiscing elit, sed do eiusmod tempor incididunt ut labore et dolore magna aliqua. Ut enim ad minim veniam, quis nostrud exercitation ullamco laboris nisi ut aliquip ex ea commodo consequat. Duis aute irure dolor in reprehenderit in voluptate velit esse cillum dolore eu fugiat nulla pariatur. Excepteur sint occaecat cupidatat non proident, sunt in culpa qui officia deserunt mollit anim id est laborum</p>
  <div class="btn" style="left:579px;top:2495px;width:196px;height:54px;font-size:18px">Read More</div>
</section>

<section class="testimonials" role="img" aria-label="Blue financial chart and coin stack backdrop">
  <h2 class="heading">Testimonials</h2>
  <div class="abs center quote-mark">&ldquo;</div>
  <p class="abs quote-text" style="text-align:center">Lorem ipsum dolor sit amet, consectetur adipiscing elit, sed do eiusmod tempor incididunt ut labore et dolore magna aliqua. Ut enim ad minim veniam, quis nostrud exercitation ullamco laboris nisi ut aliquip ex ea commodo consequat.</p>
  <div class="abs center quote-name">Mara Ellison</div>
  <svg class="abs" style="left:26px;top:350px" width="36" height="24" viewBox="0 0 36 24"><path d="M34 12H3M13 2L3 12l10 10" fill="none" stroke="#fff" stroke-width="2.5"/></svg>
  <svg class="abs" style="left:1138px;top:350px" width="36" height="24" viewBox="0 0 36 24"><path d="M2 12h31M23 2l10 10-10 10" fill="none" stroke="#fff" stroke-width="2.5"/></svg>
</section>

<section class="contact">
  <h2 class="heading" style="top:3393px">Contact <b>US</b></h2>
  <div class="field" style="left:224px;top:3468px;width:368px;height:43px;padding-top:12px">First Name</div>
  <div class="field" style="left:609px;top:3468px;width:369px;height:43px;padding-top:12px">Last Name</div>
  <div class="field" style="left:224px;top:3527px;width:368px;height:43px;padding-top:12px">Email No</div>
  <div class="field" style="left:609px;top:3527px;width:369px;height:43px;padding-top:12px">Phone No</div>
  <div class="field" style="left:224px;top:3585px;width:754px;height:98px;padding-top:12px">Message</div>
  <div class="btn" style="left:518px;top:3695px;width:166px;height:42px;font-size:16px;background:linear-gradient(90deg,var(--blue) 0%,var(--blue) 55%,var(--green) 100%)">Submit</div>
</section>

<footer>
  <div class="footer-photo" role="img" aria-label="Dark photo of business people in a meeting"></div>
  <svg class="footer-wave" width="1200" height="260" viewBox="0 0 1200 260">
    <path d="M0 0 L1200 0 L1200 90 C900 170 650 150 400 120 C250 105 100 110 0 60Z" fill="#fff"/>
    <path d="M0 0 C60 100 200 150 420 150 C700 150 950 80 1200 90 L1200 115 C950 110 700 185 420 185 C200 185 60 130 0 80Z" fill="#8cc63f"/>
  </svg>
  <div class="foot-brand">VEL-CORA<small>SOLUTIONS</small></div>
  <div class="foot-icon" style="left:254px"><svg width="34" height="40" viewBox="0 0 34 40"><path d="M17 36S5 22 5 14a12 12 0 0 1 24 0c0 8-12 22-12 22z" fill="none" stroke="#fff" stroke-width="2"/><circle cx="17" cy="14" r="4.5" fill="none" stroke="#fff" stroke-width="2"/><ellipse cx="17" cy="37" rx="10" ry="2.5" fill="none" stroke="#fff" stroke-width="1.5"/></svg></div>
  <div class="foot-icon" style="left:558px"><svg width="38" height="38" viewBox="0 0 24 24"><path d="M6.6 10.8a15 15 0 0 0 6.6 6.6l2.2-2.2c.3-.3.7-.4 1-.2 1.1.4 2.3.6 3.6.6.6 0 1 .4 1 1V20c0 .6-.4 1-1 1A17 17 0 0 1 3 4c0-.6.4-1 1-1h3.5c.6 0 1 .4 1 1 0 1.3.2 2.5.6 3.6.1.3 0 .7-.2 1z" fill="none" stroke="#fff" stroke-width="1.3"/></svg></div>
  <div class="foot-icon" style="left:862px"><svg width="44" height="32" viewBox="0 0 44 32"><rect x="2" y="2" width="40" height="28" fill="none" stroke="#fff" stroke-width="2"/><path d="M2 2l20 16L42 2M2 30l15-14M42 30L27 16" fill="none" stroke="#fff" stroke-width="2"/></svg></div>
  <p class="foot-text" style="left:116px">1180 Harbor Crest Rd.<br>Lakeview, ON L4R 2K9</p>
  <p class="foot-text" style="left:420px">Phone: 604-555-0147</p>
  <p class="foot-text" style="left:724px">Email: hello@velcorahealth.ca</p>
  <p class="abs center copyright">&copy; 2020 Company Name&nbsp; All right reserved</p>
  <span class="social" style="left:530px"></span>
  <span class="social" style="left:567px"></span>
  <span class="social" style="left:604px"></span>
  <span class="social" style="left:641px"></span>
</footer>

</body>
</html>
```